Business Card Design

We are a commercial real estate brokerage in San Francisco, leasing office buildings downtown.
I would like a clean, elegant look. Simple but powerful .

Industry/Entity Type

Business

Contact Information for Business Card

Derek Holloway
lic# 07258143
415.555.0172
derek@velt-commercial.example
velt-commercial.example

```html
<!DOCTYPE html>
<html lang="en">
<head>
<meta charset="utf-8">
<title>Velt Commercial — Business Card</title>
<link href="https://fonts.googleapis.com/css2?family=Lato:wght@400;700;900&display=swap" rel="stylesheet">
<style>
  :root {
    --stage: #000000;
    --card-light: #f3f3f3;
    --card-blue: #7889a7;
    --accent: #6d7e9e;
    --ink: #2b2b2b;
    --ink-soft: #444444;
    --mark-grey: #5a5a5a;
    --white: #ffffff;
  }
  * { margin: 0; padding: 0; box-sizing: border-box; }
  html, body { width: 1200px; height: 900px; overflow: hidden; background: var(--stage); }
  .canvas { position: relative; width: 1200px; height: 900px; background: var(--stage); font-family: "Lato", sans-serif; }

  .card { position: absolute; top: 200px; width: 310px; height: 502px; overflow: hidden; }
  .card--front { left: 265px; background: var(--card-light); border-radius: 62px 0 62px 0; }
  .card--back { left: 641px; width: 309px; background: var(--card-blue); border-radius: 0 62px 0 62px; }

  .brand { position: absolute; left: 25px; top: 48px; display: flex; align-items: center; }
  .brand__square { width: 44px; height: 44px; background: var(--accent); margin-right: 16px; }
  .brand__name { color: var(--accent); font-weight: 900; line-height: 1; }
  .brand__name .line1 { display: block; font-size: 44px; letter-spacing: 0.5px; }
  .brand__name .line2 { display: block; font-size: 20.5px; letter-spacing: 0.6px; margin-top: 3px; }

  .contact { position: absolute; left: 23px; top: 342px; color: var(--ink); }
  .contact__name { color: var(--accent); font-weight: 700; font-size: 18.5px; margin-bottom: 20px; }
  .contact__list { list-style: none; }
  .contact__item { display: flex; align-items: center; font-size: 13.5px; height: 21px; color: var(--ink); }
  .contact__item svg { width: 10px; height: 10px; margin: 0 7px 0 0; fill: var(--accent); }
  .contact__license { margin-top: 22px; font-size: 13.5px; font-weight: 700; color: var(--ink); }
  .contact__license span { color: var(--accent); }

  .back__title { position: absolute; left: 0; right: 0; top: 58px; text-align: center; color: var(--white); font-weight: 900; line-height: 1; }
  .back__title .line1 { display: block; font-size: 66px; letter-spacing: 1px; }
  .back__title .line2 { display: block; font-size: 31px; letter-spacing: 0.8px; margin-top: 4px; }
  .back__skyline { position: absolute; left: 48px; right: 0; bottom: 0; height: 275px;
    background: linear-gradient(180deg, rgba(104,120,150,0.35) 0%, rgba(100,116,146,0.6) 100%); }
</style>
</head>
<body>
<div class="canvas">
  <section class="card card--front">
    <div class="brand">
      <div class="brand__square"></div>
      <div class="brand__name"><span class="line1">VELT</span><span class="line2">COMMERCIAL</span></div>
    </div>
    <div class="contact">
      <p class="contact__name">Derek Holloway</p>
      <ul class="contact__list">
        <li class="contact__item"><svg viewBox="0 0 10 10"><path d="M2 0.5 L3.6 2.6 L2.8 3.7 C3.4 5 4.8 6.5 6.3 7.2 L7.4 6.4 L9.5 8 L8.6 9.5 C4.5 9.3 0.7 5.5 0.5 1.4 Z"/></svg>415.555.0172</li>
        <li class="contact__item"><svg viewBox="0 0 10 10"><path d="M0 2 H10 V8.5 H0 Z M0.6 2.4 L5 5.6 L9.4 2.4" stroke="#f3f3f3" stroke-width="0.8"/></svg>derek@velt-commercial.example</li>
        <li class="contact__item"><svg viewBox="0 0 10 10"><path d="M4 6 L6 4" stroke="#6d7e9e" stroke-width="1.2" fill="none"/><path d="M3.2 4.8 L1.6 6.4 A1.4 1.4 0 0 0 3.6 8.4 L5.2 6.8 M6.8 5.2 L8.4 3.6 A1.4 1.4 0 0 0 6.4 1.6 L4.8 3.2" stroke="#6d7e9e" stroke-width="1.2" fill="none"/></svg>velt-commercial.example</li>
      </ul>
      <p class="contact__license"><span>Lic#</span> 07258143</p>
    </div>
  </section>

  <section class="card card--back">
    <div class="back__title"><span class="line1">VELT</span><span class="line2">COMMERCIAL</span></div>
    <div class="back__skyline" role="img" aria-label="Faint illustration of downtown office towers rising from the bottom of the card"></div>
  </section>
</div>
</body>
</html>
```